Logistics Website Design

See website https://tqfreightglobal.com for theme and color details. Need the site to be re-done and reflect some of the designs shown in this list here: https://pixelvane.com/tags/logistics-company-website

Target Market(s)

Logistics & Transportation

Industry/Entity Type

Logistics and Supply Chain

Coding

Number of Pages Required

5+ page

Requirements
Must have
• Colors must match theme of logo. Looking for a sleek, interactive design.

```html
<!DOCTYPE html>
<html lang="en">
<head>
<meta charset="utf-8">
<title>About Us – TQ Freight Global</title>
<link href="https://fonts.googleapis.com/css2?family=Oswald:wght@300;400;500;600;700&display=swap" rel="stylesheet">
<style>
:root{
  --orange:#ef8a5e;
  --orange-deep:#e2743f;
  --black:#000;
  --ink:#2f2f2f;
  --footer:#2a2a2a;
  --white:#fff;
  --grey:#7c7c7c;
  --photo-a:#c9ccd2;
  --photo-b:#3b4252;
  --ocean-a:#0c1e3c;
  --ocean-b:#2a6aa6;
}
*{box-sizing:border-box;margin:0;padding:0}
html,body{width:1200px;height:2400px;overflow:hidden;background:var(--white);font-family:'Oswald',sans-serif}
.page{position:relative;width:1200px;height:2400px}
.abs{position:absolute}

/* header */
.story{left:0;top:0;width:1200px;height:852px;background:var(--black)}
.nav-left{left:100px;top:24px;width:540px;height:40px;background:var(--white);border-radius:10px 0 0 10px;display:flex;align-items:center;padding-left:24px;font-size:11px;font-weight:500;color:#111;text-transform:uppercase;white-space:nowrap}
.nav-left span{margin-right:52px}
.nav-left .search{margin-left:8px}
.nav-right{left:624px;top:24px;width:476px;height:40px;background:var(--orange);border-radius:0 12px 12px 0;display:flex;align-items:center;padding-left:64px;font-size:11px;font-weight:500;color:var(--white);text-transform:uppercase;white-space:nowrap}
.nav-right span{margin-right:40px}
.nav-right .active{background:var(--orange-deep);line-height:40px;padding:0 8px;margin-right:28px}
.brand-badge{left:566px;top:10px;width:70px;height:70px;border-radius:50%;background:var(--black);border:3px solid var(--orange);display:flex;align-items:center;justify-content:center;text-align:center;font-size:9px;font-weight:600;color:var(--orange);line-height:1.1}

.story-title{left:100px;top:168px;font-size:44px;font-weight:700;color:var(--white);letter-spacing:.5px}
.story-title em{font-style:normal;color:var(--orange)}
.story-body{left:100px;top:284px;width:538px;font-size:16.4px;font-weight:300;line-height:21.6px;color:var(--white);text-align:justify}
.story-body p{margin-bottom:21.6px}

.photo{border:1px solid var(--orange);border-radius:8px;background:linear-gradient(180deg,var(--photo-a),var(--photo-b))}
.photo-1{left:725px;top:150px;width:178px;height:362px}
.photo-2{left:922px;top:347px;width:177px;height:362px}
.photo-3{left:725px;top:532px;width:178px;height:244px}
.story-badge{left:834px;top:446px;width:146px;height:146px;border-radius:50%;background:var(--black);border:5px solid var(--orange);display:flex;align-items:center;justify-content:center;text-align:center;font-size:17px;font-weight:600;color:var(--orange);line-height:1.15}

/* leadership */
.lead-title{left:96px;top:936px;font-size:38px;font-weight:600;color:var(--ink);white-space:nowrap}
.lead-role{left:97px;top:984px;font-size:23px;font-weight:300;color:var(--orange);white-space:nowrap}
.lead-rule{left:100px;top:1032px;width:446px;height:1px;background:var(--orange)}
.lead-body{left:100px;top:1078px;width:602px;font-size:12.6px;font-weight:300;line-height:16.8px;color:var(--grey);text-align:justify}
.lead-body p{margin-bottom:16.8px}
.portrait{left:725px;top:880px;width:405px;height:458px;border-radius:190px 190px 0 0;background:linear-gradient(180deg,#3a2c26 0%,#2c4f8c 45%,#1f3f78 100%)}

/* footer */
.footer{left:0;top:1338px;width:1200px;height:294px;background:var(--footer);color:var(--white)}
.foot-badge{left:100px;top:1432px;width:66px;height:66px;border-radius:50%;border:3px solid var(--orange);background:var(--black);display:flex;align-items:center;justify-content:center;text-align:center;font-size:8.5px;font-weight:600;color:var(--orange);line-height:1.1}
.foot-cta{left:102px;top:1516px;font-size:13px;font-weight:500;line-height:15px;color:var(--white);text-transform:uppercase}
.foot-col{top:1428px;color:var(--white);white-space:nowrap}
.foot-col h4{font-size:13px;font-weight:500;margin-bottom:18px;text-transform:uppercase}
.foot-col ul{list-style:none}
.foot-col li{font-size:9px;font-weight:300;line-height:23px;text-transform:uppercase}
.col-links{left:426px}
.col-services{left:698px}
.col-contact{left:966px;width:150px}
.col-contact p{font-size:6.5px;font-weight:300;line-height:9px;text-transform:uppercase;white-space:normal}
.phone{font-size:23px;font-weight:600;letter-spacing:1px;margin-top:12px}
.socials{display:flex;gap:6px;margin-top:8px}
.socials span{width:16px;height:16px;border-radius:50%;background:var(--white)}

.ocean{left:0;top:1632px;width:1200px;height:202px;background:radial-gradient(ellipse at 55% 110%,var(--ocean-b) 0%,#173d6e 45%,var(--ocean-a) 100%)}
.copyright{left:0;top:1736px;width:1200px;text-align:center;font-size:20px;font-weight:600;color:var(--white)}

.page-title{left:0;top:2020px;width:1200px;text-align:center;font-size:124px;font-weight:400;color:var(--ink);letter-spacing:-1px;line-height:1}
</style>
</head>
<body>
<div class="page">

  <section class="abs story"></section>

  <nav class="abs nav-left">
    <span>Request a Quote</span>
    <span>Signup/Login</span>
    <span>Get Start</span>
    <svg class="search" width="18" height="18" viewBox="0 0 18 18" fill="none" stroke="#111" stroke-width="2"><circle cx="7.5" cy="7.5" r="5.5"/><line x1="11.5" y1="11.5" x2="16" y2="16"/></svg>
  </nav>
  <nav class="abs nav-right">
    <span>Home</span>
    <span>Services</span>
    <span>Industries</span>
    <span class="active">About Us</span>
    <span>Contact Us</span>
  </nav>
  <div class="abs brand-badge">TQ FREIGHT<br>GLOBAL</div>

  <h2 class="abs story-title"><em>OUR</em> STORY</h2>
  <div class="abs story-body">
    <p>TQ Freight Global™ was born out of real-world experience in the fitness equipment industry. What started as a company shipping strength equipment, cardio machines, and training gear to gyms, schools, and commercial facilities quickly evolved into something bigger. As order volume grew and supply chains became more complex, the team developed deep expertise in coordinating freight, managing deliveries, and navigating the challenges of large-scale equipment transportation. That hands-on experience laid the foundation for what would eventually become a full-service logistics operation.</p>
    <p>Recognizing the opportunity to build a more efficient and reliable transportation network, TQ Freight expanded beyond fitness equipment and began offering logistics services to manufacturers, distributors, and retailers across multiple industries. Today, the company supports domestic and international freight movement including LTL, truckload, specialized equipment transport, and supply chain coordination. The same operational discipline developed while shipping bulky, high-value fitness equipment now drives the company's ability to move complex freight with precision and reliability.</p>
    <p>At the center of the organization is our Founder Marcus Adeyemi, whose relentless work ethic and entrepreneurial vision have fueled the company's growth. Marcus's leadership philosophy is simple: lead from the front and understand every part of the operation firsthand. As the engine behind the company, he has built TQ Freight into a dynamic organization focused on solving real logistics challenges, delivering exceptional service, and continuously expanding its capabilities to support businesses across the country.</p>
  </div>

  <div class="abs photo photo-1" role="img" aria-label="Photo of a smiling team member in a suit holding documents"></div>
  <div class="abs photo photo-2" role="img" aria-label="Photo of two smiling team members in business attire"></div>
  <div class="abs photo photo-3" role="img" aria-label="Photo of a smiling team member in a dark blazer"></div>
  <div class="abs story-badge">TQ FREIGHT<br>GLOBAL</div>

  <h2 class="abs lead-title">LEADERSHIP TEAM</h2>
  <div class="abs lead-role">MARCUS ADEYEMI, DIRECTOR OF AGENCY SALES</div>
  <div class="abs lead-rule"></div>
  <div class="abs lead-body">
    <p>Marcus is a driven entrepreneur and the Founder of CRATEHAUS®, a rapidly growing e-commerce and wholesale operation connecting fitness brands, gyms, and buyers worldwide. A Lakeview State alumnus, Adeyemi earned national recognition as a member of Venture Weekly's "Rising 500"—an honor awarded to standout emerging entrepreneurs from over 200,000+ applicants. Built from the ground up with no outside advantages, his journey reflects resilience, grit, and a relentless commitment to innovation in the fitness and e-commerce industries.</p>
    <p>Expanding beyond retail, Adeyemi has strategically migrated into the logistics sector—leveraging his deep experience in supply chain, shipping, and fulfillment to build scalable freight and transportation solutions. This evolution positions him not just as a marketplace founder, but as a vertically integrated operator focused on controlling distribution, improving delivery efficiency, and unlocking new revenue streams across the global commerce ecosystem.</p>
  </div>
  <div class="abs portrait" role="img" aria-label="Portrait of the director in a blue suit and light blue tie"></div>

  <footer class="abs footer"></footer>
  <div class="abs foot-badge">TQ FREIGHT<br>GLOBAL</div>
  <div class="abs foot-cta">Ready to move your<br>freight?</div>
  <div class="abs foot-col col-links">
    <h4>Quick Links</h4>
    <ul><li>Home</li><li>Service</li><li>Industries</li><li>Request Quote</li><li>Contact Us</li></ul>
  </div>
  <div class="abs foot-col col-services">
    <h4>Services</h4>
    <ul><li>Full Truckload</li><li>LTL Freight</li><li>Expedited</li><li>Warehousing</li></ul>
  </div>
  <div class="abs foot-col col-contact">
    <h4>Contact Info</h4>
    <p>Reach our dispatch team any day of the week for quotes, tracking updates, and freight planning support across every lane we serve nationwide.</p>
    <div class="phone">123-456-7890</div>
    <div class="socials"><span></span><span></span><span></span></div>
  </div>

  <div class="abs ocean" role="img" aria-label="Night view of the globe with cargo ships and containers"></div>
  <div class="abs copyright">© 2026. AN INDEPENDENT AGENT OF HARLOW TRANSIT LLC.</div>

  <h1 class="abs page-title">ABOUT US</h1>
</div>
</body>
</html>
```